Marlow Estate Fixers (Handyman / Home Improvement Company)

Looking for a double sided professional looking business card with Logo attached to be highlighted on one side and throwing in an image of a handyman as an option would be nice to see as well. We are a company focused on providing quality Handyman and Home improvement services in a timely manner that is done right the first time with integrity

Industry/Entity Type

Handyman / Home Improvement

Contact Information for Business Card

(LOGO, Name, Mobile and office phone numbers, email) on front side of card, (the words "The SOLUTION to all of your Handyman and Home Improvement needs" followed by "Family Owned and Operated" at the very bottom) on the back.

Colors
EB3D1F
EC4F4E
F09395
F8D3D4
FCEDEE

Requirements
Must have
• Red, Gray, Black Color scheme
Should not have
• No Yellow or Blue colors

```html
<!DOCTYPE html>
<html lang="en">
<head>
<meta charset="utf-8">
<title>Marlow Estate Fixers – Business Card</title>
<link rel="stylesheet" href="https://fonts.googleapis.com/css2?family=Montserrat:wght@400;500;700;800&display=swap">
<style>
  :root {
    --backdrop: #2b2b2c;
    --card: #1b1b1c;
    --card-edge: #262627;
    --red: #e8282b;
    --white: #ffffff;
    --muted: #e6e6e6;
  }
  * { box-sizing: border-box; margin: 0; padding: 0; }
  html, body { width: 1200px; height: 875px; overflow: hidden; }
  body {
    background: var(--backdrop);
    font-family: "Montserrat", sans-serif;
    display: flex;
    flex-direction: column;
    align-items: center;
    justify-content: center;
    gap: 40px;
  }
  .card {
    position: relative;
    width: 620px;
    height: 354px;
    background: var(--card);
    border: 1px solid var(--card-edge);
    border-radius: 24px;
    box-shadow: 0 14px 34px rgba(0,0,0,0.45);
    overflow: hidden;
  }
  .brand {
    display: flex;
    align-items: center;
    gap: 14px;
    color: var(--white);
    font-weight: 800;
    text-transform: uppercase;
    letter-spacing: 0.02em;
    line-height: 1.1;
  }
  .brand-dot {
    flex: none;
    width: 26px;
    height: 26px;
    border-radius: 50%;
    background: var(--red);
  }

  /* Logo side */
  .card-front .brand {
    position: absolute;
    left: 50%;
    top: 132px;
    transform: translate(-50%, -50%);
    font-size: 34px;
    white-space: nowrap;
  }
  .tagline {
    position: absolute;
    left: 40px;
    right: 40px;
    bottom: 74px;
    text-align: center;
    font-size: 14px;
    font-weight: 500;
    line-height: 1.45;
    color: var(--muted);
  }
  .tagline .accent { color: var(--red); font-weight: 700; }
  .family-line {
    position: absolute;
    left: 0;
    right: 0;
    bottom: 28px;
    text-align: center;
    font-size: 11px;
    font-weight: 700;
    letter-spacing: 0.18em;
    text-transform: uppercase;
    color: var(--red);
  }

  /* Contact side */
  .card-back .brand {
    position: absolute;
    right: 40px;
    top: 108px;
    width: 250px;
    font-size: 24px;
  }
  .person { position: absolute; left: 40px; top: 52px; }
  .person-name { font-size: 24px; font-weight: 700; color: var(--white); }
  .person-name .surname { color: var(--red); }
  .person-role { font-size: 12.5px; font-weight: 400; color: var(--muted); margin-top: 2px; }
  .address {
    position: absolute; left: 40px; top: 168px;
    font-size: 13px; line-height: 1.35; color: var(--muted);
  }
  .contacts {
    position: absolute; left: 40px; top: 218px;
    list-style: none; font-size: 13px; color: var(--muted);
  }
  .contacts li { display: flex; align-items: center; gap: 10px; line-height: 24px; }
  .contacts .label { color: var(--red); font-weight: 700; width: 14px; }
  .contacts svg { width: 13px; height: 13px; fill: var(--red); flex: none; }
</style>
</head>
<body>
  <section class="card card-front" aria-label="Card logo side">
    <div class="brand"><span class="brand-dot"></span>Marlow Estate Fixers</div>
    <p class="tagline">The <span class="accent">SOLUTION</span> to all of your Handyman<br>and Home Improvement needs</p>
    <p class="family-line">Family Owned and Operated</p>
  </section>

  <section class="card card-back" aria-label="Card contact side">
    <div class="person">
      <p class="person-name">Owen <span class="surname">Hartley</span></p>
      <p class="person-role">Managing Director</p>
    </div>
    <p class="address">48 Alder Lane,<br>Marlow, USA</p>
    <ul class="contacts">
      <li>
        <svg viewBox="0 0 16 16" aria-hidden="true"><path d="M4.5 1h7a1 1 0 0 1 1 1v12a1 1 0 0 1-1 1h-7a1 1 0 0 1-1-1V2a1 1 0 0 1 1-1Zm.5 2v9h6V3Zm3 10a.8.8 0 1 0 0 .01Z"/></svg>
        Mobile: (08) 4410 2286
      </li>
      <li>
        <svg viewBox="0 0 16 16" aria-hidden="true"><path d="M3.5 1 6 4.5 4.6 6.2c.8 2 2.2 3.4 4.2 4.2L10.5 9 14 11.5 12.6 15C6.5 14.5 1.5 9.5 1 3.4Z"/></svg>
        Office: (08) 4410 2290
      </li>
      <li>
        <svg viewBox="0 0 16 16" aria-hidden="true"><path d="M1 3h14v10H1Zm1.5 1.3v.4L8 8.6l5.5-3.9v-.4Z"/></svg>
        hello@marlowfixers.com
      </li>
      <li>
        <svg viewBox="0 0 16 16" aria-hidden="true"><circle cx="8" cy="8" r="7"/></svg>
        www.marlowfixers.com
      </li>
    </ul>
    <div class="brand"><span class="brand-dot"></span>Marlow Estate Fixers</div>
  </section>
</body>
</html>
```